Veldmark Supplies Business Card

Professional business card that stand out to our potential customers. Front and back with clean modern design

Industry/Entity Type

Oil and gas

Contact Information for Business Card

Name, address, website , office phone and cell number

Requirements
Must have
• Editable files for each employee

```html
<!DOCTYPE html>
<html lang="en">
<head>
<meta charset="utf-8">
<title>Veldmark Supplies Business Card</title>
<link rel="stylesheet" href="https://fonts.googleapis.com/css2?family=Montserrat:wght@400;700&display=swap">
<style>
  :root {
    --brand-red: #ed1c24;
    --brand-cyan: #10b0d4;
    --ink: #231f20;
    --paper: #ffffff;
    --backdrop: #e4e5e7;
  }
  * { margin: 0; padding: 0; box-sizing: border-box; }
  html, body {
    width: 1200px; height: 1059px; overflow: hidden;
    background: var(--backdrop);
    font-family: "Montserrat", sans-serif;
    color: var(--ink);
  }
  .card {
    position: absolute;
    background: var(--paper);
  }
  .card--front { left: 256px; top: 100px; width: 688px; height: 391px; }
  .card--back  { left: 253px; top: 537px; width: 694px; height: 394px; }

  .brand {
    position: absolute;
    display: flex; align-items: center; gap: 10px;
    font-weight: 700; color: var(--brand-red);
    letter-spacing: 0.02em; white-space: nowrap;
  }
  .brand__square { background: var(--brand-cyan); flex: none; }
  .card--front .brand { right: 30px; top: 152px; font-size: 19px; }
  .card--front .brand__square { width: 22px; height: 22px; }
  .card--back .brand {
    left: 50%; top: 50%; transform: translate(-50%, -50%);
    font-size: 36px;
  }
  .card--back .brand__square { width: 40px; height: 40px; }

  .person { position: absolute; left: 31px; top: 186px; }
  .person__name {
    font-size: 30px; font-weight: 700; line-height: 1; letter-spacing: 0.01em;
  }
  .person__first { color: var(--brand-red); }
  .person__last { color: var(--brand-cyan); }
  .person__role {
    margin-top: 8px; font-size: 16px; font-weight: 400; letter-spacing: 0.06em;
  }
  .contact { list-style: none; margin-top: 10px; }
  .contact__item {
    display: flex; align-items: center; gap: 8px;
    height: 23.3px; font-size: 16.5px; letter-spacing: 0.02em;
  }
  .contact__icon { width: 13px; height: 13px; flex: none; }
</style>
</head>
<body>
  <section class="card card--front" aria-label="Business card front">
    <div class="brand"><span class="brand__square"></span>VELDMARK SUPPLIES</div>

    <div class="person">
      <h1 class="person__name"><span class="person__first">DANIEL</span> <span class="person__last">HARROW</span></h1>
      <p class="person__role">MANAGER</p>
      <ul class="contact">
        <li class="contact__item">
          <svg class="contact__icon" viewBox="0 0 24 24"><path fill="#ed1c24" d="M6.6 10.8a15 15 0 0 0 6.6 6.6l2.2-2.2c.3-.3.7-.4 1-.2 1.1.4 2.3.6 3.6.6.6 0 1 .4 1 1V20c0 .6-.4 1-1 1A17 17 0 0 1 3 4c0-.6.4-1 1-1h3.5c.6 0 1 .4 1 1 0 1.3.2 2.5.6 3.6.1.3 0 .7-.2 1z"/></svg>
          1-604-555-0148
        </li>
        <li class="contact__item">
          <svg class="contact__icon" viewBox="0 0 24 24"><path fill="#10b0d4" d="M2 5h20v14H2z"/><path fill="none" stroke="#fff" stroke-width="1.8" d="M2 6l10 7 10-7"/></svg>
          dharrow@kestrelparts.vn
        </li>
        <li class="contact__item">
          <svg class="contact__icon" viewBox="0 0 24 24" fill="none" stroke="#ed1c24" stroke-width="2"><circle cx="12" cy="12" r="10"/><ellipse cx="12" cy="12" rx="4.5" ry="10"/><path d="M2 12h20M4 7h16M4 17h16"/></svg>
          www.kestrelparts.vn
        </li>
        <li class="contact__item">
          <svg class="contact__icon" viewBox="0 0 24 24" fill="none" stroke="#10b0d4" stroke-width="2"><circle cx="12" cy="12" r="10"/><ellipse cx="12" cy="12" rx="4.5" ry="10"/><path d="M2 12h20M4 7h16M4 17h16"/></svg>
          www.kestrelparts.com
        </li>
        <li class="contact__item">
          <svg class="contact__icon" viewBox="0 0 24 24"><path fill="#ed1c24" d="M12 1a8 8 0 0 0-8 8c0 6 8 14 8 14s8-8 8-14a8 8 0 0 0-8-8zm0 11a3 3 0 1 1 0-6 3 3 0 0 1 0 6z"/></svg>
          Ho Chi Minh, Vietnam
        </li>
      </ul>
    </div>
  </section>

  <section class="card card--back" aria-label="Business card back">
    <div class="brand"><span class="brand__square"></span>VELDMARK SUPPLIES</div>
  </section>
</body>
</html>
```